Business Card Design Project : Ridgeline Press

In preparation for market launch, Tamarind's Ridgeline Press require the development of a business card. Ridgeline Press is a Community online publishing web portal. We provide the the city of Whistler located in B.C. (Canada) business directories, News, Classified ads, News, Events and blogs etc.

The main focus of the brand is to help local businesses to corporate with their online advertisement and marketing. Meeting our clients face to face is a must (B2B).

Target Market(s)

The target market is B2B customers. Business Owners to Marketing, advertising Managers

Industry/Entity Type

Business

Requirements
Must have
• - The business card will be two sided.
the BACK side will have our logo which consist of (icon, url,slogan) submited. The logo will be middle and centred.

The FRONT side should have company details:

Company Legal Name: TAMARIND RIDGELINE MEDIA

Owen Farsk
Director of Sales & Marketing

www.tamarindridgeline.biz
owen@tamarindridgeline.biz

Phone: 604 317 8842
#2714 - 582 E. Halvern St.
Vancouver, B.C. V7K2R4 Canada
Nice to have
• - For the "FRONT" side of our business card. You can separate or re-arrange with our logo components (icon, logo,slogan). It does not have to be together.

Also our company legal name is rather long so arrange or organize the name in a way to make it shorter. Your experience and creativity will have to come in play.
Should not have
• should not have other colors beside logo color and black text (2 colors). Also nothing Three dimensional

```html
<!DOCTYPE html>
<html lang="en">
<head>
<meta charset="utf-8">
<title>Ridgeline Press – Business Card</title>
<link rel="stylesheet" href="https://fonts.googleapis.com/css2?family=Source+Sans+3:ital,wght@0,400;0,600;0,700;0,800;1,400&display=swap">
<style>
  :root {
    --stage: #070808;
    --paper: #ffffff;
    --brand-blue: #2f8cf5;
    --ink: #111111;
  }
  * { box-sizing: border-box; margin: 0; padding: 0; }
  html, body {
    width: 1200px;
    height: 900px;
    overflow: hidden;
    background: var(--stage);
    font-family: "Source Sans 3", "Myriad Pro", Arial, sans-serif;
  }
  .stage { position: relative; width: 1200px; height: 900px; }

  .card {
    position: absolute;
    background: var(--paper);
  }
  .card--front { left: 133px; top: 124px; width: 549px; height: 314px; }
  .card--back  { left: 480px; top: 439px; width: 552px; height: 315px; }

  /* Front */
  .company-block {
    position: absolute;
    left: 0; top: 88px;
    width: 171px; height: 138px;
    background: var(--brand-blue);
    color: var(--paper);
    text-align: right;
    padding: 18px 8px 0 0;
    font-weight: 700;
    font-size: 23px;
    line-height: 21px;
    letter-spacing: -0.2px;
    text-transform: uppercase;
  }
  .contact {
    position: absolute;
    left: 177px; top: 105px;
    color: var(--brand-blue);
  }
  .contact__name { font-size: 23px; font-weight: 600; line-height: 26px; }
  .contact__title { font-size: 16px; font-style: italic; line-height: 20px; }
  .contact__web { font-size: 13.5px; line-height: 20px; margin-top: 2px; }
  .contact__row {
    display: flex; align-items: center; gap: 8px;
    font-size: 13.5px; line-height: 20px;
  }
  .contact__row svg { width: 19px; height: 14px; flex: none; }

  /* Back */
  .brand-lockup {
    position: absolute;
    left: 0; right: 0; top: 104px;
    display: flex; flex-direction: column; align-items: center; gap: 10px;
  }
  .brand-lockup__dot {
    width: 44px; height: 44px; border-radius: 50%;
    background: var(--brand-blue);
  }
  .brand-lockup__name {
    font-size: 24px; font-weight: 700; color: var(--ink);
    letter-spacing: -0.3px;
  }
</style>
</head>
<body>
<main class="stage">
  <section class="card card--front" aria-label="Business card front">
    <div class="company-block">Tamarind<br>Ridgeline<br>Media</div>
    <div class="contact">
      <p class="contact__name">Owen Farsk</p>
      <p class="contact__title">Director of Sales &amp; Marketing</p>
      <p class="contact__web">www.tamarindridgeline.biz / owen@tamarindridgeline.biz</p>
      <p class="contact__row">
        <svg viewBox="0 0 19 14" aria-hidden="true">
          <path fill="currentColor" d="M1 5c2-4 15-4 17 0l-1 2-4-1V4H6v2L2 7z"/>
          <rect fill="currentColor" x="3" y="8" width="13" height="6" rx="1"/>
          <circle fill="#fff" cx="9.5" cy="11" r="1.6"/>
        </svg>
        604 317 8842
      </p>
      <p class="contact__row">
        <svg viewBox="0 0 19 14" aria-hidden="true">
          <rect x="1" y="1" width="17" height="12" fill="none" stroke="currentColor" stroke-width="1.6"/>
          <path d="M1 1l8.5 7L18 1M1 13l6-6M18 13l-6-6" fill="none" stroke="currentColor" stroke-width="1.4"/>
        </svg>
        #2714 - 582 E. Halvern St. Vancouver, B.C. V7K2R4 Canada
      </p>
    </div>
  </section>

  <section class="card card--back" aria-label="Business card back">
    <div class="brand-lockup">
      <span class="brand-lockup__dot" aria-hidden="true"></span>
      <p class="brand-lockup__name">www.tamarindridgeline.biz</p>
    </div>
  </section>
</main>
</body>
</html>
```